Brightmill Data Works

Our company is about IT hardwares and IT solutions. IT hardware such as PC, RAMS, storage and servers. IT solutions such as project management, BA. We are also selling new technology too.

Target Market(s)

Consumer, Small to Medium Business, Corporate

Requirements
Must have
• The business card must have the following:
• Name:
• Title:
• Contact Number:
• Email address:
• Website:
• Color: Must match the logo color upgrade

```html
<!DOCTYPE html>
<html lang="en">
<head>
<meta charset="utf-8">
<title>Brightmill Data Works – Business Card</title>
<link rel="stylesheet" href="https://fonts.googleapis.com/css2?family=Rajdhani:wght@600;700&family=Roboto:wght@400;500&display=swap">
<style>
  :root {
    --canvas: #e9e6e2;
    --card-white: #ffffff;
    --ink-grey: #5a5a5c;
    --ink-dark: #3a3a3c;
    --orange: #d9822b;
    --orange-deep: #c2621f;
    --orange-light: #e49a3d;
    --on-orange: #ffffff;
  }
  * { box-sizing: border-box; margin: 0; padding: 0; }
  html, body { width: 1200px; height: 950px; overflow: hidden; }
  body {
    background: var(--canvas);
    font-family: "Roboto", Arial, sans-serif;
    position: relative;
  }
  .card {
    position: absolute;
    left: 250px;
    width: 700px;
    height: 400px;
    overflow: hidden;
    box-shadow: 0 6px 18px rgba(0,0,0,.18);
  }
  .card--front { top: 55px; background: var(--card-white); }
  .card--back {
    top: 495px;
    background: radial-gradient(circle at 62% 38%, var(--orange-light) 0%, var(--orange) 45%, var(--orange-deep) 100%);
  }

  /* front */
  .brand {
    position: absolute;
    left: 60px;
    bottom: 60px;
    display: flex;
    align-items: center;
    gap: 14px;
  }
  .brand__mark {
    width: 22px; height: 22px;
    background: var(--orange);
  }
  .brand__name {
    font-family: "Rajdhani", "Arial Narrow", sans-serif;
    font-weight: 700;
    font-size: 34px;
    letter-spacing: 1px;
    text-transform: uppercase;
    color: var(--ink-grey);
    white-space: nowrap;
  }
  .contact {
    position: absolute;
    left: 430px;
    top: 50px;
    width: 215px;
  }
  .contact__name {
    font-family: "Rajdhani", "Arial Narrow", sans-serif;
    font-weight: 700;
    font-size: 26px;
    letter-spacing: .5px;
    color: var(--orange);
    text-transform: uppercase;
  }
  .contact__title {
    font-family: "Rajdhani", "Arial Narrow", sans-serif;
    font-weight: 600;
    font-size: 19px;
    color: var(--ink-dark);
    text-transform: uppercase;
    margin-top: 2px;
  }
  .contact__rule {
    height: 1px;
    background: var(--orange);
    margin: 16px -55px 14px 0;
  }
  .contact__list { list-style: none; }
  .contact__item {
    display: flex;
    align-items: center;
    gap: 10px;
    font-size: 16px;
    color: var(--ink-dark);
    line-height: 30px;
    white-space: nowrap;
  }
  .contact__icon { width: 14px; height: 14px; flex: none; }

  /* back */
  .back-brand {
    position: absolute;
    left: 60px;
    top: 60px;
    color: var(--on-orange);
  }
  .back-brand__name {
    font-family: "Rajdhani", "Arial Narrow", sans-serif;
    font-weight: 700;
    font-size: 38px;
    letter-spacing: 1px;
    text-transform: uppercase;
  }
  .back-brand__web {
    font-size: 15px;
    letter-spacing: 4px;
    margin-top: 6px;
  }
</style>
</head>
<body>

<section class="card card--front" aria-label="Business card front">
  <div class="contact">
    <p class="contact__name">Daniel Reyes</p>
    <p class="contact__title">CEO/Founder</p>
    <div class="contact__rule"></div>
    <ul class="contact__list">
      <li class="contact__item">
        <svg class="contact__icon" viewBox="0 0 24 24"><path fill="var(--orange)" d="M6.6 10.8a15.1 15.1 0 0 0 6.6 6.6l2.2-2.2c.3-.3.7-.4 1-.2 1.1.4 2.3.6 3.6.6.6 0 1 .4 1 1V20c0 .6-.4 1-1 1A17 17 0 0 1 3 4c0-.6.4-1 1-1h3.5c.6 0 1 .4 1 1 0 1.3.2 2.5.6 3.6.1.3 0 .7-.2 1z"/></svg>
        555 208 4417
      </li>
      <li class="contact__item">
        <svg class="contact__icon" viewBox="0 0 24 24"><rect x="2" y="5" width="20" height="14" rx="2" fill="var(--orange)"/><path d="M3 6l9 7 9-7" fill="none" stroke="#fff" stroke-width="1.8"/></svg>
        daniel@brightmill.com
      </li>
      <li class="contact__item">
        <svg class="contact__icon" viewBox="0 0 24 24"><circle cx="12" cy="12" r="10" fill="var(--orange)"/><path d="M2 12h20M12 2c3 3 3 17 0 20M12 2c-3 3-3 17 0 20" fill="none" stroke="#fff" stroke-width="1.4"/></svg>
        www.brightmill.com
      </li>
    </ul>
  </div>

  <div class="brand">
    <span class="brand__mark"></span>
    <span class="brand__name">Brightmill Data Works</span>
  </div>
</section>

<section class="card card--back" aria-label="Business card back">
  <div class="back-brand">
    <p class="back-brand__name">Brightmill Data Works</p>
    <p class="back-brand__web">www.brightmill.com</p>
  </div>
</section>

</body>
</html>
```